Professional violinist needs business cards

I am trying to attract the following jobs:
-private violin lessons (primarily classical)
-performance gigs (weddings, birthday parties, funerals, etc.)
-collaborations with other artists (studio recordings, performances)

I want to communicate that I have a very high standard of excellence for my work, but I also love people and celebrations.
Values/style words I like are:
love, joy, peace, fun, beauty, authenticity, excellence, warmth, refined/sleek, free spirited. If that's too confusing, just ignore :)

I will attach my favorite business card template that I could find on Canva. The lines are supposed to be like a music staff, which I think is really cool, but I also don't want it to look too busy. I like the simple black and white--I think it looks sharp--but I also am open to other ideas. I also have seen business cards with pictures included that looked great, so I attached an image that could be used as well.

I am also attaching a file that I made of my initials that could be used as a logo, but I'm not sure if it should be included.

Information on the card:
-My name (18 letters total)
-"violinist"
-phone number, email, website

Thank you!

```html
<!DOCTYPE html>
<html lang="en">
<head>
<meta charset="utf-8">
<title>Mara Ellison – Violinist Business Card</title>
<link href="https://fonts.googleapis.com/css2?family=Montserrat:wght@600;700&family=Arimo:wght@400&display=swap" rel="stylesheet">
<style>
  :root {
    --backdrop: #b9b9bb;
    --card: #ffffff;
    --ink: #1a1a1a;
    --ink-soft: #2b2b2b;
    --photo-stone: #6e6250;
    --photo-dark: #2a2620;
    --photo-light: #8f8573;
  }
  * { margin: 0; padding: 0; box-sizing: border-box; }
  html, body {
    width: 1200px; height: 900px; overflow: hidden;
    background: var(--backdrop);
  }
  .sheet {
    position: relative; width: 1200px; height: 900px;
    display: flex; flex-direction: column; align-items: center;
    justify-content: center; gap: 46px;
  }
  .card {
    position: relative; width: 660px; height: 377px;
    background: var(--card); border-radius: 26px; overflow: hidden;
  }

  /* Back side */
  .card--back { display: flex; align-items: center; justify-content: center; }
  .brand-mark {
    font-family: "Montserrat", sans-serif; font-weight: 600;
    font-size: 50px; color: var(--ink); letter-spacing: 1px;
    display: flex; align-items: center; gap: 18px;
  }
  .brand-mark__dot {
    width: 22px; height: 22px; border-radius: 50%; background: var(--ink);
  }

  /* Front side */
  .portrait {
    position: absolute; left: 0; top: 92px; width: 305px; height: 285px;
    background: linear-gradient(135deg, var(--photo-light) 0%, var(--photo-stone) 45%, var(--photo-dark) 100%);
  }
  .front-brand {
    position: absolute; left: 370px; top: 62px;
    font-family: "Montserrat", sans-serif; font-weight: 600;
    font-size: 30px; color: var(--ink);
    display: flex; align-items: center; gap: 12px;
  }
  .front-brand__dot { width: 14px; height: 14px; border-radius: 50%; background: var(--ink); }
  .identity { position: absolute; left: 352px; top: 178px; }
  .identity__name {
    font-family: "Montserrat", sans-serif; font-weight: 700;
    font-size: 25px; color: var(--ink);
  }
  .identity__role {
    font-family: "Arimo", sans-serif; font-size: 17px;
    color: var(--ink-soft); margin-top: 2px;
  }
  .contacts {
    position: absolute; left: 368px; top: 252px; list-style: none;
    font-family: "Arimo", sans-serif; font-size: 16px; color: var(--ink);
  }
  .contacts__item { display: flex; align-items: center; gap: 10px; height: 26px; }
  .contacts__icon { width: 18px; height: 18px; flex: none; }
</style>
</head>
<body>
<main class="sheet">

  <section class="card card--back" aria-label="Card back">
    <div class="brand-mark"><span class="brand-mark__dot"></span>Mara Ellison</div>
  </section>

  <section class="card card--front" aria-label="Card front">
    <div class="portrait" role="img" aria-label="Photo of the violinist in a black dress holding her violin beside a stone wall and stairway"></div>

    <div class="front-brand"><span class="front-brand__dot"></span>Mara Ellison</div>

    <div class="identity">
      <h1 class="identity__name">Mara Ellison</h1>
      <p class="identity__role">Violinist</p>
    </div>

    <ul class="contacts">
      <li class="contacts__item">
        <svg class="contacts__icon" viewBox="0 0 20 20" aria-hidden="true">
          <rect x="1" y="1" width="18" height="18" rx="3" fill="none" stroke="currentColor" stroke-width="1.6"/>
          <path d="M6.5 5c1 0 1.5 2 1 2.8l-.8.8c.6 1.5 1.7 2.6 3.2 3.2l.8-.8c.8-.5 2.8 0 2.8 1 0 1.2-1 2-2.2 2C8 14 5 11 5 7.2 5 6 5.5 5 6.5 5z" fill="currentColor"/>
        </svg>
        044-555 210 347
      </li>
      <li class="contacts__item">
        <svg class="contacts__icon" viewBox="0 0 20 20" aria-hidden="true">
          <path d="M1 4h18v12H1z" fill="currentColor"/>
          <path d="M1 4l9 7 9-7" fill="none" stroke="#fff" stroke-width="1.4"/>
        </svg>
        hello@maraellison.com
      </li>
      <li class="contacts__item">
        <svg class="contacts__icon" viewBox="0 0 20 20" aria-hidden="true">
          <circle cx="10" cy="10" r="9" fill="currentColor"/>
          <g fill="none" stroke="#fff" stroke-width="1">
            <ellipse cx="10" cy="10" rx="4" ry="8.6"/>
            <path d="M1.5 10h17M3 5.5h14M3 14.5h14M10 1v18"/>
          </g>
        </svg>
        www.maraellison.com
      </li>
    </ul>
  </section>

</main>
</body>
</html>
```